Home Page Design (+50 More Pages To Winning Designer!)

We have a 50+ page website, but we're starting with the home page. The winning designer will get all 50+ pages to design as a 2nd project, so make sure you do your best!

Velorane is in the private jet industry and needs a re-designed website.

We have created the structure for the website and content inside of Frandle.io (THESE ARE ONLY ROUGH A.I. GENERATED WIREFRAMES AND DO NOT NEED TO BE FOLLOWED EXACTLY) - https://www.frandle.io/app/project/K482915_qWmRtZaLs-KDnHoUvvy82QJ5cfhaR61trkwqlDV3Hm

Take the content from the 'Home Page' under the 'Wireframe' tab on the Frandle.io link above, but feel free to re-design the page in a better way as these are only A.I. generated wireframes.

We want a DARK theme.... High quality, luxurious feel, greyscale colors. Attached is a brand guideline (BUT THIS IS NOT A 100% BRAND GUIDELINE, YOU CAN CHANGE COLORS AND FONTS AND MAKE CHANGES IF YOU HAVE BETTER IDEAS) and attached is our logo. We are also attaching some examples of other apps and websites to give you a guideline of what we're looking for for this design project.

The final design MUST communicate luxury using high-quality imagery of large cabin luxurious private jets.
Updates

ENTRIES THAT DO NOT FOLLOW THE PROJECT BRIEF WILL BE AUTOMATICALLY DISCARDED. FOLLOW THE INSTRUCTIONS!

Industry/Entity Type

Travel

Number of Pages Required

1 page

Font styles to use
Sans Serif

Colors

Designer to choose colors to be used in the design.

Requirements
Must have
• Follow wireframe and use content in wireframe (see Frandle.io link)

```html
<!DOCTYPE html>
<html lang="en">
<head>
<meta charset="UTF-8">
<title>Velorane — Home Page Mobile Screens</title>
<link href="https://fonts.googleapis.com/css2?family=Exo+2:wght@400;500;600&display=swap" rel="stylesheet">
<style>
  :root {
    --canvas: #2b2b2b;
    --screen-black: #060606;
    --screen-dark: #1a1a1a;
    --card: #161616;
    --white: #ffffff;
    --text-soft: #d4d4d4;
    --border: #8a8a8a;
  }
  * { box-sizing: border-box; margin: 0; padding: 0; }
  html, body { width: 1200px; height: 1200px; overflow: hidden; }
  body {
    background: var(--canvas);
    font-family: "Exo 2", sans-serif;
    color: var(--white);
    position: relative;
  }
  .screen { position: absolute; overflow: hidden; }
  .screen--hero { left: 38px; top: 370px; width: 356px; height: 830px; background: var(--screen-black); }
  .screen--ownership { left: 420px; top: 0; width: 356px; height: 1200px; background: var(--screen-dark); }
  .screen--services { left: 802px; top: 0; width: 357px; height: 1200px; background: var(--screen-black); }

  .abs { position: absolute; }
  .brand { left: 9px; top: 30px; display: flex; align-items: center; gap: 6px; font-size: 30px; font-weight: 400; letter-spacing: 0.2px; }
  .brand-mark { width: 20px; height: 20px; background: var(--white); border-radius: 3px; }
  .menu { left: 329px; top: 38px; width: 24px; }
  .menu span { display: block; height: 3px; background: var(--white); margin-bottom: 5px; border-radius: 1px; }

  .headline { font-size: 38px; line-height: 55px; font-weight: 500; letter-spacing: 0.2px; }
  .eyebrow { font-size: 12px; color: var(--text-soft); }
  .body-copy { font-size: 12px; line-height: 18px; color: var(--text-soft); }

  .btn {
    position: absolute; display: flex; align-items: center; justify-content: center;
    border-radius: 6px; font-size: 16px; font-weight: 500; height: 53px;
  }
  .btn--solid { background: var(--white); color: #111; }
  .btn--outline { border: 1.5px solid var(--border); color: var(--white); }

  .phone-visual {
    left: 18px; top: 624px; width: 320px; height: 206px;
    background: linear-gradient(160deg, #1a1a1a 0%, #3d3d3d 45%, #8c8c8c 100%);
    border-radius: 20px 20px 0 0;
  }

  .jet-photo {
    left: 10px; top: 60px; width: 333px; height: 336px;
    background: linear-gradient(180deg, #b9cadb 0%, #c9c2b2 38%, #d8d8d8 62%, #8b7551 82%, #6f5a3b 100%);
    clip-path: polygon(9% 0, 100% 0, 91% 100%, 0 100%);
    border-radius: 10px;
  }
  .feature-list { left: 8px; top: 922px; list-style: none; }
  .feature-list li { display: flex; align-items: center; gap: 9px; height: 42px; font-size: 17px; color: var(--text-soft); }
  .jet-icon { width: 26px; height: 22px; flex: none; }

  .service-card { left: 41px; width: 276px; background: var(--card); border-radius: 4px; }
  .service-card h3 { font-size: 20px; line-height: 28px; font-weight: 500; }
  .service-card p { font-size: 12px; line-height: 19px; color: var(--text-soft); }

  .cta-band {
    left: 0; top: 615px; width: 357px; height: 522px;
    background: linear-gradient(180deg, #4d6461 0%, #6d7370 35%, #596a70 60%, #2f5064 82%, #1b3548 100%);
    text-align: center;
  }
</style>
</head>
<body>

<!-- Hero screen -->
<section class="screen screen--hero">
  <div class="abs brand"><span>Velorane</span><span class="brand-mark"></span></div>
  <div class="abs menu"><span></span><span></span><span></span></div>
  <h1 class="abs headline" style="left:10px; top:115px;">Experience The<br>Ultimate In<br>Luxury Jet Travel</h1>
  <p class="abs body-copy" style="left:9px; top:306px; width:336px;">Velorane Is A Company That Offers Fractional Jet Ownership, Jet Card Programs, Private Jet Lease Programs, All Access Programs, Helicopter Access Programs, And By The Seat Charter Flights. We Provide Flexible And Convenient Options For Individuals And Businesses To Access Private Aviation Services.</p>
  <div class="btn btn--solid" style="left:9px; top:462px; width:338px;">Explore</div>
  <div class="btn btn--outline" style="left:9px; top:538px; width:338px;">Learn More</div>
  <div class="abs phone-visual" role="img" aria-label="Mobile app screen showing the Velorane member dashboard on a grey curved backdrop"></div>
</section>

<!-- Ownership screen -->
<section class="screen screen--ownership">
  <div class="abs jet-photo" role="img" aria-label="Private jet taking off from a runway with hills behind"></div>
  <p class="abs eyebrow" style="left:9px; top:420px;">Discover</p>
  <h2 class="abs headline" style="left:9px; top:472px;">Experience The<br>Ultimate In<br>Luxury Jet Travel</h2>
  <p class="abs" style="left:9px; top:666px; width:340px; font-size:16px; line-height:28.6px; color:var(--text-soft);">With Velorane's Fractional Jet Ownership Program, You Can Enjoy The Benefits Of Private Jet Travel Without The Hassle And Expense Of Owning A Whole Aircraft. Our Program Offers Flexibility, Convenience, And Access To A Fleet Of Luxurious Jets, Allowing You To Travel In Style And Comfort.</p>
  <ul class="abs feature-list">
    <li><svg class="jet-icon" viewBox="0 0 26 22"><path d="M2 12 L24 10 L24 13 L2 14 Z M8 12 L13 3 L15 3 L13 12 Z M8 13 L13 20 L15 20 L13 13 Z M2 12 L1 7 L3 7 L5 12 Z" fill="#fff"/></svg>Flexible Ownership Options</li>
    <li><svg class="jet-icon" viewBox="0 0 26 22"><path d="M2 12 L24 10 L24 13 L2 14 Z M8 12 L13 3 L15 3 L13 12 Z M8 13 L13 20 L15 20 L13 13 Z M2 12 L1 7 L3 7 L5 12 Z" fill="#fff"/></svg>Convenient Booking Process</li>
    <li><svg class="jet-icon" viewBox="0 0 26 22"><path d="M2 12 L24 10 L24 13 L2 14 Z M8 12 L13 3 L15 3 L13 12 Z M8 13 L13 20 L15 20 L13 13 Z M2 12 L1 7 L3 7 L5 12 Z" fill="#fff"/></svg>Luxurious Fleet Of Jets</li>
  </ul>
  <div class="btn btn--solid" style="left:9px; top:1059px; width:338px;">Learn More</div>
  <div class="btn btn--outline" style="left:9px; top:1136px; width:338px;">Sign Up</div>
</section>

<!-- Services screen -->
<section class="screen screen--services">
  <article class="abs service-card" style="top:-20px; height:188px;">
    <svg class="abs jet-icon" style="left:21px; top:12px;" viewBox="0 0 26 22"><path d="M2 12 L24 10 L24 13 L2 14 Z M8 12 L13 3 L15 3 L13 12 Z M8 13 L13 20 L15 20 L13 13 Z M2 12 L1 7 L3 7 L5 12 Z" fill="#fff"/></svg>
    <h3 class="abs" style="left:20px; top:54px; width:250px;">Global Medical Response &amp; Recovery</h3>
    <p class="abs" style="left:20px; top:131px; width:240px;">We Provide Specialized Medical Transportation Services Worldwide.</p>
  </article>
  <article class="abs service-card" style="top:191px; height:194px;">
    <svg class="abs jet-icon" style="left:21px; top:22px;" viewBox="0 0 26 22"><path d="M2 12 L24 10 L24 13 L2 14 Z M8 12 L13 3 L15 3 L13 12 Z M8 13 L13 20 L15 20 L13 13 Z M2 12 L1 7 L3 7 L5 12 Z" fill="#fff"/></svg>
    <h3 class="abs" style="left:20px; top:78px; width:250px;">Fractional Jet Ownership</h3>
    <p class="abs" style="left:20px; top:138px; width:230px;">Enjoy The Benefits Of Owning A Private Jet Without The Hassles.</p>
  </article>
  <div class="btn btn--solid" style="left:9px; top:409px; width:338px;">Explore</div>
  <div class="btn btn--outline" style="left:9px; top:485px; width:338px;">Learn More</div>

  <div class="abs cta-band" role="img" aria-label="Background of a private jet wing above the clouds at dusk">
    <p class="abs eyebrow" style="left:0; width:357px; top:52px;">Discover</p>
    <h2 class="abs headline" style="left:0; width:357px; top:93px;">Experience The<br>Ultimate In<br>Luxury Jet Travel</h2>
    <p class="abs" style="left:10px; width:337px; top:282px; font-size:16px; line-height:21px; color:var(--text-soft);">Contact Us Today To Book Your Exclusive Jet Experience</p>
    <div class="btn btn--solid" style="left:9px; top:346px; width:338px;">Explore</div>
    <div class="btn btn--outline" style="left:9px; top:423px; width:338px;">Learn More</div>
  </div>
</section>

</body>
</html>
```